Verlindo Magician

I want the business card for my business to give to people who watch that later I will be employed to show magic here is my website http://www.balsamomagicien.com/I want the interesting design , i am very opened for formal and informal, I watch a lot of design so don't stick to the common shape and form but i hope it can also be produced the thing to write on will be the same as in picture that i will upload , i also will upload the logo for you that so can be easy to useDenis CostilleMagicianMAGICIAN BALSAMO 17 rue des Tilleuls - 25000 BESANÇON contact@verlindoillusions.example tel. 0381 946 157 tel. 0674 219 503

```html
<!DOCTYPE html>
<html lang="en">
<head>
<meta charset="utf-8">
<title>Verlindo Magician – Business Card</title>
<link href="https://fonts.googleapis.com/css2?family=Poppins:wght@300;400;700&display=swap" rel="stylesheet">
<style>
  :root {
    --bg: #ebe8e4;
    --card: #ffffff;
    --red: #ec2326;
    --ink: #0d0d0d;
    --grey: #555555;
    --pattern-light: #fbf9f9;
    --pattern-mid: #f1eded;
    --pattern-rose: #f7ecec;
  }
  * { margin: 0; padding: 0; box-sizing: border-box; }
  html, body {
    width: 1125px; height: 1200px; overflow: hidden;
    background: var(--bg);
    font-family: "Poppins", Arial, sans-serif;
  }
  .canvas { position: relative; width: 1125px; height: 1200px; }
  .card {
    position: absolute; left: 150px; width: 826px; height: 470px;
    background: var(--card); overflow: hidden;
    box-shadow: 0 3px 8px rgba(0,0,0,.25);
  }
  .card--front { top: 99px; }
  .card--back { top: 631px; }

  /* Front */
  .front__band {
    position: absolute; left: 0; top: 0; width: 240px; height: 470px;
    background: var(--red);
  }
  .front__portrait {
    position: absolute; left: 112px; top: 4px; width: 262px; height: 466px;
    border-radius: 70px 70px 0 0;
    background: linear-gradient(180deg, #1c1c1c 0%, #050505 60%, #1a1a1a 100%);
    border: 5px solid #fff; border-bottom: none;
  }

  .contact { position: absolute; left: 419px; top: 108px; color: var(--grey); }
  .contact__name { font-size: 32px; font-weight: 700; color: var(--ink); line-height: 36px; letter-spacing: .2px; }
  .contact__role { font-size: 22px; font-weight: 400; color: var(--red); line-height: 28px; }
  .contact__company { margin-top: 12px; font-size: 19px; font-weight: 400; line-height: 25px; text-transform: uppercase; }
  .contact__address { font-size: 19px; font-weight: 400; line-height: 25px; }
  .contact__list { list-style: none; margin-top: 12px; }
  .contact__item { display: flex; align-items: center; gap: 9px; font-size: 19px; font-weight: 400; line-height: 26.5px; }
  .contact__icon { width: 17px; height: 17px; fill: var(--ink); flex: none; }

  /* Back */
  .back__pattern {
    position: absolute; inset: 0;
    background: linear-gradient(135deg, var(--pattern-light) 0%, var(--pattern-mid) 35%, var(--pattern-rose) 65%, var(--pattern-mid) 100%);
  }
  .back__emblem {
    position: absolute; left: 318px; top: 88px; width: 190px; height: 236px;
    border-radius: 70px 70px 20px 20px;
    background: linear-gradient(180deg, #151515 0%, #000 100%);
  }
  .back__brand {
    position: absolute; left: 0; right: 0; top: 330px; text-align: center;
    font-size: 31px; font-weight: 300; color: var(--ink); letter-spacing: 1px;
  }
</style>
</head>
<body>
<div class="canvas">
  <section class="card card--front">
    <div class="front__band"></div>
    <div class="front__portrait" role="img" aria-label="Black and white illustration of the magician in a dark jacket holding a playing card"></div>
    <div class="contact">
      <h1 class="contact__name">MARC RAVOULET</h1>
      <p class="contact__role">Magician</p>
      <p class="contact__company">Magician Verlindo</p>
      <p class="contact__address">17 rue des Tilleuls - 25000 BESANÇON</p>
      <ul class="contact__list">
        <li class="contact__item">
          <svg class="contact__icon" viewBox="0 0 24 24"><path d="M6.6 10.8a15.1 15.1 0 0 0 6.6 6.6l2.2-2.2a1 1 0 0 1 1-.25 11.4 11.4 0 0 0 3.6.57 1 1 0 0 1 1 1V20a1 1 0 0 1-1 1A17 17 0 0 1 3 4a1 1 0 0 1 1-1h3.5a1 1 0 0 1 1 1c0 1.25.2 2.45.57 3.6a1 1 0 0 1-.25 1z"/></svg>
          0381 946 157</li>
        <li class="contact__item">
          <svg class="contact__icon" viewBox="0 0 24 24"><path d="M6.6 10.8a15.1 15.1 0 0 0 6.6 6.6l2.2-2.2a1 1 0 0 1 1-.25 11.4 11.4 0 0 0 3.6.57 1 1 0 0 1 1 1V20a1 1 0 0 1-1 1A17 17 0 0 1 3 4a1 1 0 0 1 1-1h3.5a1 1 0 0 1 1 1c0 1.25.2 2.45.57 3.6a1 1 0 0 1-.25 1z"/></svg>
          0674 219 503</li>
        <li class="contact__item">
          <svg class="contact__icon" viewBox="0 0 24 24"><path d="M2 6h20v12H2z M3.5 7.5l8.5 6 8.5-6" fill="none" stroke="#0d0d0d" stroke-width="2"/></svg>
          contact@verlindoillusions.example</li>
        <li class="contact__item">
          <svg class="contact__icon" viewBox="0 0 24 24"><circle cx="12" cy="12" r="9"/><path d="M8 7c2 1 1 3 3 3s1 3-1 4M15 15c1-2 3-1 4-3" fill="none" stroke="#fff" stroke-width="1.6"/></svg>
          www.verlindoillusions.example</li>
      </ul>
    </div>
  </section>

  <section class="card card--back">
    <div class="back__pattern" role="img" aria-label="Faint repeating pattern of grey and pink playing-card suits"></div>
    <div class="back__emblem" role="img" aria-label="Small black illustration of the magician holding a playing card"></div>
    <p class="back__brand">VERLINDO MAGICIAN</p>
  </section>
</div>
</body>
</html>
```